BRIGHT RIVER POWER.

I'd like my business logo.
contact name: Dennis Halvorsen
phone:0438759164
email: info@brightriverpower.net.au
website: www.brightriverpower.net.au

services:
solar
battery storage
LED lighting
energy saving solutions
general electrical
I'd like the design to look professional

Target Market(s)

Everyone

Industry/Entity Type

Business

Contact Information for Business Card

as described above

Requirements
Must have
• Id like the colours and the design to work well with my logo.

```html
<!DOCTYPE html>
<html lang="en">
<head>
<meta charset="utf-8">
<title>Bright River Power – Business Card</title>
<link rel="stylesheet" href="https://fonts.googleapis.com/css2?family=Open+Sans:wght@400;600;700&display=swap">
<style>
  :root {
    --bg: #e9e6e1;
    --orange-light: #f7a631;
    --orange: #f08a12;
    --orange-deep: #e07a0a;
    --green-light: #8cc63f;
    --green: #5aaa2e;
    --green-deep: #3f8f22;
    --white: #ffffff;
    --stripe: #f2a43a;
  }
  * { margin: 0; padding: 0; box-sizing: border-box; }
  html, body {
    width: 1200px; height: 843px; overflow: hidden;
    background: var(--bg);
    font-family: "Open Sans", Arial, sans-serif;
  }
  .canvas {
    width: 1200px; height: 843px;
    display: flex; align-items: center; justify-content: center; gap: 40px;
  }
  .card {
    position: relative;
    width: 540px; height: 330px;
    border-radius: 18px;
    overflow: hidden;
    box-shadow: 0 10px 30px rgba(0,0,0,0.18);
  }
  /* Back side */
  .card-back {
    background: linear-gradient(135deg, var(--orange-light) 0%, var(--orange) 55%, var(--orange-deep) 100%);
    color: var(--white);
    display: flex; flex-direction: column; align-items: center; justify-content: center;
  }
  .brand {
    display: flex; align-items: center; gap: 14px;
    font-weight: 700; letter-spacing: 0.5px;
  }
  .brand-dot { border-radius: 50%; flex: none; }
  .card-back .brand { font-size: 30px; color: var(--white); }
  .card-back .brand-dot { width: 34px; height: 34px; background: var(--white); }
  .services {
    margin-top: 26px;
    font-size: 13px; font-weight: 400; letter-spacing: 0.4px;
  }
  /* Front side */
  .card-front { background: var(--white); }
  .wave { position: absolute; inset: 0; width: 100%; height: 100%; }
  .card-front .brand {
    position: absolute; top: 92px; right: 34px;
    font-size: 26px; color: var(--green);
  }
  .card-front .brand-dot { width: 30px; height: 30px; background: var(--orange); }
  .contact {
    position: absolute; left: 40px; top: 138px;
    color: var(--white);
  }
  .contact-name {
    font-size: 19px; font-weight: 600; letter-spacing: 0.6px;
    text-transform: uppercase; margin-bottom: 12px;
  }
  .contact-line {
    display: flex; align-items: center; gap: 9px;
    font-size: 14px; line-height: 24px;
  }
  .contact-line svg { width: 13px; height: 13px; flex: none; fill: var(--white); }
</style>
</head>
<body>
<main class="canvas">
  <section class="card card-back" aria-label="Card back">
    <div class="brand"><span class="brand-dot"></span>BRIGHT RIVER POWER</div>
    <p class="services">Solar • Battery Storage • LED Lighting</p>
  </section>

  <section class="card card-front" aria-label="Card front">
    <svg class="wave" viewBox="0 0 540 330" preserveAspectRatio="none" aria-hidden="true">
      <defs>
        <linearGradient id="greenFill" x1="0" y1="0" x2="1" y2="1">
          <stop offset="0" stop-color="#4fa52c"/>
          <stop offset="0.5" stop-color="#7dbf3a"/>
          <stop offset="1" stop-color="#5aaa2e"/>
        </linearGradient>
      </defs>
      <path d="M0,112 C150,80 270,120 350,200 C410,262 470,292 540,288" fill="none" stroke="var(--stripe)" stroke-width="5"/>
      <path d="M0,124 C150,94 262,140 338,218 C400,280 470,306 540,300 L540,330 L0,330 Z" fill="url(#greenFill)"/>
    </svg>

    <div class="brand"><span class="brand-dot"></span>BRIGHT RIVER POWER</div>

    <div class="contact">
      <p class="contact-name">Dennis Halvorsen</p>
      <p class="contact-line">
        <svg viewBox="0 0 24 24"><path d="M6.6 10.8a15.1 15.1 0 0 0 6.6 6.6l2.2-2.2a1 1 0 0 1 1-.25 11.4 11.4 0 0 0 3.6.57 1 1 0 0 1 1 1V20a1 1 0 0 1-1 1A17 17 0 0 1 3 4a1 1 0 0 1 1-1h3.5a1 1 0 0 1 1 1c0 1.25.2 2.45.57 3.57a1 1 0 0 1-.25 1z"/></svg>
        0438759164
      </p>
      <p class="contact-line">
        <svg viewBox="0 0 24 24"><path d="M2 5h20v14H2z M2 5l10 8 10-8" /></svg>
        info@brightriverpower.net.au
      </p>
      <p class="contact-line">
        <svg viewBox="0 0 24 24"><circle cx="12" cy="12" r="10"/></svg>
        www.brightriverpower.net.au
      </p>
    </div>
  </section>
</main>
</body>
</html>
```